Corvane Freight Company Business Card Design

We are a company that delivers natural saltwater (from the ocean) to aquarium companies, restaurants and home marine tanks. I would like a new business card to suit.

Must include Name, company name, abn, contact number and website as well as logo (see attached).

Looking for a design that stands out, has a clean but unique appearance.

Double and single sided entries welcome

Business

• Logo

```html
<!DOCTYPE html>
<html lang="en">
<head>
<meta charset="utf-8">
<title>Corvane Freight Company – Business Card</title>
<link rel="stylesheet" href="https://fonts.googleapis.com/css2?family=Source+Sans+3:wght@400;600;700&display=swap">
<style>
  :root {
    --backdrop: #1c1c1c;
    --brand-blue: #0b5fae;
    --sky-line: #56c3f0;
    --logo-blue: #1a8fd0;
    --card-white: #ffffff;
    --ink: #222222;
    --ink-soft: #555555;
  }
  * { box-sizing: border-box; margin: 0; padding: 0; }
  html, body {
    width: 1200px; height: 420px; overflow: hidden;
    background: var(--backdrop);
    font-family: "Source Sans 3", sans-serif;
  }
  .canvas { position: relative; width: 1200px; height: 420px; }

  .card {
    position: absolute; top: 65px;
    width: 516px; height: 293px; overflow: hidden;
  }
  .card--front { left: 66px; background: var(--card-white); }
  .card--back { left: 618px; background: var(--brand-blue); }

  .band { position: absolute; left: 0; width: 100%; background: var(--brand-blue); }
  .band--top { top: 0; height: 33px; }
  .band--bottom { bottom: 0; height: 31px; }
  .rule { position: absolute; left: 0; width: 100%; height: 3px; background: var(--sky-line); }
  .rule--top { top: 36px; }
  .rule--bottom { bottom: 35px; }

  .wordmark {
    position: absolute; left: 26px; top: 112px;
    display: flex; align-items: center; gap: 8px;
    color: var(--logo-blue); font-weight: 600; font-size: 30px;
    letter-spacing: -0.5px; line-height: 1;
  }
  .wordmark__dot {
    width: 14px; height: 14px; border-radius: 50%; background: var(--sky-line);
  }

  .holder {
    position: absolute; left: 0; width: 340px; top: 208px;
    text-align: center; color: var(--ink-soft); font-size: 17px;
  }
  .holder__name { font-weight: 700; }

  .contact {
    position: absolute; left: 340px; top: 90px;
    color: var(--ink); font-size: 14px; line-height: 20px;
  }
  .contact p { white-space: nowrap; }
  .contact__abn { margin-top: 14px; }
  .contact__lines { margin-top: 26px; }
  .contact__line { display: flex; align-items: center; gap: 6px; }
  .contact__line svg { width: 11px; height: 11px; }

  .back-mark {
    position: absolute; inset: 0;
    display: flex; align-items: center; justify-content: center; gap: 14px;
    color: var(--card-white); font-weight: 600; font-size: 52px; letter-spacing: -1px;
  }
  .back-mark__dot {
    width: 26px; height: 26px; border-radius: 50%; background: var(--sky-line);
  }
</style>
</head>
<body>
<main class="canvas">
  <section class="card card--front" aria-label="Business card front">
    <div class="band band--top"></div>
    <div class="rule rule--top"></div>

    <div class="wordmark">
      <span class="wordmark__dot"></span>
      <span class="wordmark__name">Corvane Freight</span>
    </div>

    <p class="holder"><span class="holder__name">Your Name,</span> Title</p>

    <div class="contact">
      <p>Street Name, City Name</p>
      <p>State, Zip Code</p>
      <p class="contact__abn">ABN: 123456789</p>
      <div class="contact__lines">
        <p class="contact__line">
          <svg viewBox="0 0 12 12" aria-hidden="true"><path d="M3 1l2 2.5-1.2 1.2a7 7 0 0 0 3.5 3.5L8.5 7 11 9l-1.5 2C5 11 1 7 1 2.5z" fill="none" stroke="#222" stroke-width="1.2"/></svg>
          123-456-7892
        </p>
        <p class="contact__line">
          <svg viewBox="0 0 12 12" aria-hidden="true"><g fill="none" stroke="#222" stroke-width="1"><circle cx="6" cy="6" r="5"/><ellipse cx="6" cy="6" rx="2.2" ry="5"/><path d="M1 6h10M2 3.3h8M2 8.7h8"/></g></svg>
          www.corvanefreight.com
        </p>
      </div>
    </div>

    <div class="rule rule--bottom"></div>
    <div class="band band--bottom"></div>
  </section>

  <section class="card card--back" aria-label="Business card back">
    <div class="back-mark">
      <span class="back-mark__dot"></span>
      <span class="back-mark__name">Corvane Freight</span>
    </div>
  </section>
</main>
</body>
</html>
```